Basic / Quick Business Card

Quick easy design project!

Need a one sided basic business card that matches font & style of brand and bottle label for our gourmet condiment, Brindle Harrow Sauce. Brindle Harrow Sauce is sold in specialty retail, gourmet groceries and appears on chef-driven restaurant menus, so the target market is a high end, gourmet, artisan-made food-loving customer.

Files Included:
Sauce Bottle Label
Brindle Harrow Sauce Round Logos

**About the logos - the logo may be used in a circle or alone vertically as on side of the bottle label**

Layout of Card:
May be vertical or horizontal based on designer ideas.

Logo usage (in circle vs. stand alone vertical logo) is up to designers descretion as well.

Reverse side of business card will be various high end / professional product photos / food shots using us.kelbo.com system. **Designer on this project will NOT design a reserve for the card.**

Paper that will be used for printing:
Kelbo Standard - it's a WHITE paper, but we use a cream background on Brindle Harrow Sauce branding, so please take this into account on design to stay brand consistent.

Elements & Copy for Card:
1. Logo in either script horizontal or vertical version
2. Copy: "Artisan Made - Small Batch"
3. Name - Wes Dorrance
4. Title - Creator
5. Phone - xxx.xxx.xxxx
6. xxxx@brindleharrow.com
7. URL: brindleharrowsauce.com
8. Social Media: @getbrindleharrow on Quillo / Pagora / Lumigrid

Please provide final files in Illustrator or InDesign format.

```html
<!DOCTYPE html>
<html lang="en">
<head>
<meta charset="utf-8">
<title>Brindle Harrow Sauce – Business Card</title>
<link rel="stylesheet" href="https://fonts.googleapis.com/css2?family=Open+Sans:wght@400;600;700&family=Crimson+Text:wght@400&display=swap">
<style>
  :root {
    --backdrop: #e7e4df;
    --card: #ffffff;
    --ink: #1f1d1e;
    --band: #231f20;
    --gold: #f0b323;
    --muted: #3a3738;
    --light: #ffffff;
  }
  * { box-sizing: border-box; margin: 0; padding: 0; }
  html, body {
    width: 1200px; height: 804px; overflow: hidden;
    background: var(--backdrop);
  }
  .card {
    position: absolute; left: 50px; top: 87px;
    width: 1100px; height: 630px;
    background: var(--card);
    box-shadow: 0 6px 24px rgba(0,0,0,0.12);
    overflow: hidden;
    font-family: "Open Sans", Arial, sans-serif;
    color: var(--ink);
  }
  .card-shapes { position: absolute; inset: 0; }
  .brand-mark {
    position: absolute; left: 100px; top: 170px;
    font-weight: 600; color: var(--ink); line-height: 0.98;
  }
  .brand-mark .brand-name { display: block; font-size: 78px; letter-spacing: -1px; }
  .brand-mark .brand-sub { display: block; font-size: 30px; letter-spacing: 10px; margin: 8px 0 0 150px; }
  .origin-note {
    position: absolute; left: 96px; top: 504px;
    font-family: "Crimson Text", Georgia, serif;
    font-size: 23px; line-height: 1.15; color: var(--ink);
  }
  .contact-block { position: absolute; left: 640px; top: 205px; width: 390px; }
  .person-name { font-weight: 700; font-size: 34px; line-height: 1.2; }
  .person-title { font-size: 26px; margin-top: 2px; }
  .divider {
    margin: 18px 0 24px; height: 0;
    border-top: 4px dotted var(--gold); width: 372px;
  }
  .contact-list { list-style: none; }
  .contact-list li {
    display: flex; align-items: center; gap: 12px;
    font-size: 22.5px; line-height: 1; height: 40px; color: var(--muted);
  }
  .contact-list svg { width: 24px; height: 24px; flex: none; }
  .social-row {
    position: absolute; left: 655px; top: 560px;
    transform: translateY(-50%);
    display: flex; align-items: center; gap: 16px;
    white-space: nowrap;
    color: var(--light); font-size: 24px; line-height: 1;
  }
  .social-row .social-item { display: flex; align-items: center; gap: 6px; font-size: 17px; }
  .social-row .dot { width: 14px; height: 14px; border-radius: 50%; background: var(--gold); flex: none; }
</style>
</head>
<body>
  <div class="card">
    <svg class="card-shapes" width="1100" height="630" viewBox="0 0 1100 630" aria-hidden="true">
      <polygon points="0,575 580,575 565,605 0,605" fill="var(--gold)"/>
      <polygon points="0,612 561,612 552,630 0,630" fill="var(--band)"/>
      <path d="M612 490 L612 195 L770 80 L1040 140 L1040 500" fill="none" stroke="var(--gold)" stroke-width="11" stroke-linejoin="miter"/>
      <polygon points="640,490 1100,490 1100,630 570,630" fill="var(--band)"/>
    </svg>

    <div class="brand-mark">
      <span class="brand-name">Brindle</span>
      <span class="brand-name">Harrow</span>
      <span class="brand-sub">sauce</span>
    </div>

    <p class="origin-note">made in mississippi<br>Artisan Made - Small Batch</p>

    <div class="contact-block">
      <h1 class="person-name">Wes Dorrance</h1>
      <p class="person-title">Creator</p>
      <div class="divider"></div>
      <ul class="contact-list">
        <li>
          <svg viewBox="0 0 24 24"><circle cx="12" cy="12" r="10.5" fill="none" stroke="var(--ink)" stroke-width="2"/><path d="M8.5 6.5c-1 1-1 3 .8 5.6s4 4 5.6 4.2c1 .1 1.8-.5 2.3-1.3l-2.2-1.6-1.2 1c-1.3-.5-2.8-2-3.4-3.4l1-1.2-1.6-2.2z" fill="var(--ink)"/></svg>
          <span>555-014-2388</span>
        </li>
        <li>
          <svg viewBox="0 0 24 24"><path d="M2 10 L12 3 L22 10 V20 H2 Z" fill="var(--ink)"/><path d="M2 10 L12 16 L22 10" fill="none" stroke="#fff" stroke-width="1.6"/></svg>
          <span>wdorrance@brindleharrow.com</span>
        </li>
        <li>
          <svg viewBox="0 0 24 24"><circle cx="12" cy="12" r="10" fill="none" stroke="var(--ink)" stroke-width="2"/><ellipse cx="12" cy="12" rx="4.2" ry="10" fill="none" stroke="var(--ink)" stroke-width="1.6"/><path d="M2 12h20M4 7h16M4 17h16" stroke="var(--ink)" stroke-width="1.4"/></svg>
          <span>www.brindleharrowsauce.com</span>
        </li>
      </ul>
    </div>

    <div class="social-row">
      <span>Follow Us On</span>
      <span class="social-item"><span class="dot"></span>Pagora</span>
      <span class="social-item"><span class="dot"></span>Quillo</span>
      <span class="social-item"><span class="dot"></span>Lumigrid</span>
    </div>
  </div>
</body>
</html>
```